Mobile app for checking bus arrival

I would like to make the UI much more beautiful and modern. The app is an app to check bus arrival in Singapore.
See here: https://apps.veltrano.com/store/apps/details?id=com.ridoka&hl=en

Based on the question from designers:

1. The first screen shows the favorite bus stop. Each item shows location / street, the top one is the location, second line is the street name. And the number is the bus stop code.

2. Please download the app and try bus stop code with 07589 or 10079, for example. It will bring you to the next screen.

3. The pencil allow you to select color theme, for the list item, and the header.

4. On the second screen, it will show up the list of bus route that available on that bus stop.

5. When you tap on one of them it will show you the 2 subsequent arrival time.

6. Each of the arrival time has the information of availability seats available, seats not available, no more space. (we can use green, yellow, red, respectively).

7. Each of the arrival time has the WAB indicator (Wheelchair availability). Show as icon is preferred.

7. KLT and VOPN are the bus provider in Singapore. 48 means the route /service no.

Requirements:
And check the attachment, see screen 3. I need to add information about the space availability, which has 3 state: seats available, seats not available, no more space. (we can use green, yellow, red, respectively).

Please advise how to show the information.

Target Market(s)

Students, age below 35

Industry/Entity Type

Trivex

Requirements
Must have
• The app currently has the capabilities to select color theme, checkout screen1. It's the button and the list item color.
Nice to have
• Please download the app to see all available colors, and make suggestion to have better color pallete.

```html
<!DOCTYPE html>
<html lang="en">
<head>
<meta charset="utf-8">
<title>Bus Arrival – Stop 07589</title>
<link rel="stylesheet" href="https://fonts.googleapis.com/css2?family=Montserrat:wght@400;500&display=swap">
<style>
:root{
  --bg:#4a4d55;
  --blue:#4a7cf0;
  --red:#e24a48;
  --purple:#a046e0;
  --tile-grey:#e9e9e9;
  --white:#ffffff;
  --green:#3fbf4a;
  --amber:#f2b90c;
  --ad-dark:#6a3a0c;
  --ad-light:#d98a1e;
}
*{box-sizing:border-box;margin:0;padding:0}
html,body{width:1200px;height:900px;overflow:hidden}
body{background:var(--bg);font-family:"Montserrat",sans-serif;display:flex;align-items:center;justify-content:center}
.screen{width:460px;height:818px;background:var(--white);position:relative;overflow:hidden;display:flex;flex-direction:column}
.app-bar{background:var(--blue);color:var(--white);padding:0 16px 14px}
.status-bar{height:30px;display:flex;align-items:center;justify-content:space-between;font-size:13px}
.status-left,.status-right{display:flex;align-items:center;gap:6px}
.signal{letter-spacing:1px;font-size:10px}
.battery{width:24px;height:11px;border:1px solid var(--white);border-radius:2px;position:relative}
.battery::after{content:"";position:absolute;left:1px;top:1px;width:5px;height:7px;background:var(--white)}
.nav-row{display:flex;align-items:center;justify-content:space-between;height:40px}
.stop-code{font-size:22px;letter-spacing:1px}
.actions{display:flex;gap:16px;align-items:center}
.title-row{display:flex;align-items:center;gap:14px}
.stop-name{text-align:center;flex:1;margin-right:34px}
.stop-name h1{font-weight:400;font-size:24px}
.stop-name p{font-size:12px;opacity:.9}
.grid{flex:1;display:grid;grid-template-columns:1fr 1fr;gap:8px;padding:8px;align-content:start}
.col{display:flex;flex-direction:column;gap:8px}
.tile{height:150px;position:relative;display:flex;align-items:center;justify-content:center}
.tile .route{font-size:40px;font-weight:400}
.tile .op{position:absolute;left:14px;bottom:10px;font-size:16px}
.tile-red{background:var(--red);color:var(--white)}
.tile-purple{background:var(--purple);color:var(--white)}
.tile-grey{background:var(--tile-grey)}
.tile-grey.red-text{color:var(--red)}
.tile-grey.purple-text{color:var(--purple)}
.detail{height:110px;padding:6px 4px}
.wab{display:flex;align-items:center;background:var(--red);color:var(--white);height:28px;font-size:15px}
.wab-label{display:flex;align-items:center;gap:8px;padding:0 10px;flex:1}
.wab-time{background:var(--white);color:var(--red);border:2px solid var(--red);height:28px;padding:0 12px;display:flex;align-items:center}
.loads{display:flex;gap:14px;margin-top:16px;padding-left:18px}
.load{width:36px;height:36px;border-radius:50%;color:var(--white);display:flex;align-items:center;justify-content:center;font-size:15px}
.load-seats{background:var(--green)}
.load-full{background:var(--red)}
.load-stand{background:var(--amber)}
.ad-banner{position:absolute;left:0;right:0;bottom:0;height:72px;display:flex;align-items:center;gap:16px;padding:0 18px;color:var(--white)}
.ad-art{position:absolute;inset:0;background:linear-gradient(90deg,var(--ad-dark),var(--ad-light) 60%,var(--ad-dark))}
.ad-copy{position:relative;font-size:17px;line-height:1.1}
.ad-brand{position:relative;margin-left:auto;font-size:20px}
</style>
</head>
<body>
<main class="screen">
  <header class="app-bar">
    <div class="status-bar">
      <div class="status-left"><span class="signal">●●●○○</span><span>KESTRA</span></div>
      <span>4:21 PM</span>
      <div class="status-right"><span>22%</span><span class="battery"></span></div>
    </div>
    <div class="nav-row">
      <svg width="14" height="22" viewBox="0 0 14 22"><path d="M11 3 3 11l8 8" fill="none" stroke="#fff" stroke-width="2"/></svg>
      <span class="stop-code">07589</span>
      <div class="actions">
        <svg width="22" height="22" viewBox="0 0 24 24"><path d="M12 2l3 7h7l-5.6 4.3 2.1 7.2L12 16.3 5.5 20.5l2.1-7.2L2 9h7z" fill="#fff"/></svg>
        <svg width="22" height="22" viewBox="0 0 24 24"><path d="M5 12a7 7 0 1 0 2-5" fill="none" stroke="#fff" stroke-width="2.4"/><path d="M3 3v6h6" fill="none" stroke="#fff" stroke-width="2.4"/></svg>
        <svg width="6" height="20" viewBox="0 0 6 20"><circle cx="3" cy="3" r="2" fill="#fff"/><circle cx="3" cy="10" r="2" fill="#fff"/><circle cx="3" cy="17" r="2" fill="#fff"/></svg>
      </div>
    </div>
    <div class="title-row">
      <svg width="20" height="22" viewBox="0 0 20 24"><path d="M10 22s7-7 7-12a7 7 0 0 0-14 0c0 5 7 12 7 12z" fill="none" stroke="#fff" stroke-width="1.8"/><circle cx="10" cy="10" r="2.5" fill="none" stroke="#fff" stroke-width="1.6"/></svg>
      <div class="stop-name"><h1>Opp lindell ctr</h1><p>marwen rd</p></div>
    </div>
  </header>

  <section class="grid">
    <div class="col">
      <div class="detail">
        <div class="wab">
          <span class="wab-label">
            <svg width="20" height="18" viewBox="0 0 20 18"><rect x="2" y="2" width="16" height="11" rx="2" fill="none" stroke="#fff" stroke-width="1.6"/><circle cx="6" cy="15" r="1.6" fill="#fff"/><circle cx="14" cy="15" r="1.6" fill="#fff"/></svg>
            WAB
          </span>
          <span class="wab-time">120</span>
        </div>
        <div class="loads">
          <span class="load load-seats">7</span>
          <span class="load load-full">21</span>
          <span class="load load-stand">100</span>
        </div>
      </div>
      <div class="tile tile-red"><span class="route">131</span><span class="op">klt</span></div>
      <div class="tile tile-grey purple-text"><span class="route">960</span><span class="op">vopn</span></div>
      <div class="tile tile-purple"><span class="route">2N</span></div>
    </div>
    <div class="col">
      <div class="tile tile-red"><span class="route">57</span><span class="op">klt</span></div>
      <div class="tile tile-grey red-text"><span class="route">851</span><span class="op">vopn</span></div>
      <div class="tile tile-purple"><span class="route">2N</span><span class="op">klt</span></div>
      <div class="tile tile-grey"></div>
    </div>
  </section>

  <aside class="ad-banner">
    <div class="ad-art" role="img" aria-label="Warm golden photograph backdrop of the test advertisement banner"></div>
    <p class="ad-copy">320x50<br>Test Banner</p>
    <span class="ad-brand">Bannerly</span>
  </aside>
</main>
</body>
</html>
```